New Business Card Design for Manufacturing

We are an engineering/manufacturing company that offers Advanced machining/assembly/engineering services, as well as innovative products for the heavy duty engine cooling markets.

We are looking to get a new business card designed that is clean and modern looking, but still fits the wide range of technical/skilled work we do.

- We hope to use this design as the base for other design work in new Presentations, web, and print work.

Industry/Entity Type

Engineering

Contact Information for Business Card

Our preferred color of blue is (RGB) 22/71/159 but can vary slightly from that color. Our content will be our Logo and full company name (Vantrell Forge Works, Inc.), company address, name, job title, phone number with extension, cell number, fax number, website, and email address on the cards.
We'd like the full company name next to the logo, but we are open to other interpretations of that layout.
Preferably, we would like the back side to be clean with just our logo, and the front to contain all of the contact information.

Colors
2f74b4
0355a3
85abd2

Requirements
Must have
• - Logo, company name, needed content - We are open to interpretation beyond that.
• - Standard size business card.
• - Horizontal orientation.
• - Enough space for lengthy names / job titles (for example, a job title could read "Directory of Human Resources" or "V.P. of Governmental Affairs"). We need this to look clean, whether the title be short (CEO) or long (as described above).

```html
<!DOCTYPE html>
<html lang="en">
<head>
<meta charset="utf-8">
<title>Vantrell Forge Works – Business Card</title>
<link href="https://fonts.googleapis.com/css2?family=Work+Sans:wght@400;500;700&display=swap" rel="stylesheet">
<style>
  :root {
    --brand-blue: #16479f;
    --swoosh-grey: #6f7378;
    --text-dark: #1d1f22;
    --text-muted: #7a7d82;
    --card-white: #fbfbfa;
    --stage: #e9eaec;
  }
  * { margin: 0; padding: 0; box-sizing: border-box; }
  html, body { width: 1200px; height: 891px; overflow: hidden; }
  body {
    background: var(--stage);
    font-family: "Work Sans", Arial, sans-serif;
    display: flex;
    align-items: center;
    justify-content: center;
    gap: 50px;
  }
  .card {
    position: relative;
    width: 525px;
    height: 300px;
    background: var(--card-white);
    border-radius: 4px;
    box-shadow: 0 6px 18px rgba(0,0,0,0.12);
    overflow: hidden;
  }
  .card-shapes { position: absolute; inset: 0; }
  .brand-name {
    position: absolute;
    color: var(--brand-blue);
    font-weight: 700;
    line-height: 1.05;
  }
  .card-front .brand-name { left: 32px; top: 30px; font-size: 22px; }
  .person {
    position: absolute;
    left: 300px;
    top: 112px;
  }
  .person-name {
    color: var(--brand-blue);
    font-weight: 700;
    font-size: 20px;
    letter-spacing: 0.5px;
    text-transform: uppercase;
  }
  .person-title {
    color: var(--text-muted);
    font-size: 9.5px;
    letter-spacing: 0.6px;
    text-transform: uppercase;
    margin-top: 3px;
  }
  .address {
    margin-top: 14px;
    color: var(--text-dark);
    font-size: 11px;
    font-weight: 500;
    line-height: 1.45;
  }
  .contact-list {
    position: absolute;
    right: 230px;
    top: 216px;
    list-style: none;
    color: #fff;
    font-size: 11px;
    line-height: 17px;
    text-align: right;
  }
  .contact-list li { display: flex; justify-content: flex-end; align-items: center; gap: 7px; }
  .contact-icon { width: 12px; height: 12px; flex: none; }
  .contact-icon.blank { visibility: hidden; }
  .card-back .brand-name {
    left: 0; right: 0; top: 112px;
    text-align: center;
    font-size: 30px;
  }
  .website {
    position: absolute;
    left: 0; right: 0; top: 228px;
    text-align: center;
    font-size: 11px;
    letter-spacing: 3px;
    color: var(--text-dark);
  }
  .website .domain { color: var(--brand-blue); }
</style>
</head>
<body>

  <section class="card card-front" aria-label="Business card front">
    <svg class="card-shapes" viewBox="0 0 525 300" width="525" height="300" aria-hidden="true">
      <path d="M0,115 C80,190 190,214 320,220 C415,225 485,248 525,278 L525,300 L0,300 Z" fill="var(--brand-blue)"/>
      <path d="M35,62 C80,140 170,190 300,206" fill="none" stroke="var(--swoosh-grey)" stroke-width="7" stroke-linecap="round"/>
      <path d="M60,92 C110,150 190,186 290,200" fill="none" stroke="var(--brand-blue)" stroke-width="4" stroke-linecap="round"/>
    </svg>

    <div class="brand-name">Vantrell Forge Works</div>

    <div class="person">
      <div class="person-name">Dorian Kessler</div>
      <div class="person-title">Directory of Human Resources</div>
      <div class="address">
        44 P/O Box Harlow Road,<br>
        210 Mill Street Drive.
      </div>
    </div>

    <ul class="contact-list">
      <li>(555) 210.4471.118
        <svg class="contact-icon" viewBox="0 0 12 12"><circle cx="6" cy="6" r="6" fill="#fff"/><path d="M4 3.2 L5 3 L5.6 4.6 L5 5.1 Q5.6 6.5 6.9 7 L7.4 6.4 L9 7 L8.8 8 Q6.5 8.4 4.9 6.8 Q3.5 5.3 4 3.2Z" fill="var(--brand-blue)"/></svg>
      </li>
      <li>(555) 364. 8820.905
        <svg class="contact-icon blank" viewBox="0 0 12 12"></svg>
      </li>
      <li>555-732-1904
        <svg class="contact-icon" viewBox="0 0 12 12"><circle cx="6" cy="6" r="6" fill="#fff"/><rect x="3" y="5" width="6" height="3.2" rx="0.6" fill="var(--brand-blue)"/><rect x="4" y="3" width="4" height="2" fill="var(--brand-blue)"/></svg>
      </li>
      <li>info@vantrellforge.com
        <svg class="contact-icon" viewBox="0 0 12 12"><circle cx="6" cy="6" r="6" fill="#fff"/><rect x="3" y="4" width="6" height="4.2" fill="var(--brand-blue)"/><path d="M3 4 L6 6.3 L9 4" fill="none" stroke="#fff" stroke-width="0.7"/></svg>
      </li>
    </ul>
  </section>

  <section class="card card-back" aria-label="Business card back">
    <div class="brand-name">Vantrell Forge Works, Inc.</div>
    <div class="website">www.<span class="domain">vantrellforge</span>.com</div>
  </section>

</body>
</html>
```